Zelvo Stationary

Design the stationary of Zelvo Promotions Group.

Zelvo is a BTL company, BTL meaning "below the line". In other words Zelvo is a Promotional Marketing company (the company that design the brands promotional activities).

The design should transmit creativity, agility, boldness.

I need:
* Bis Card
* Letter head
* Envelopes, both vertical and horizontal (for legal size), and letter envelope
* Folders
* PPT template (Title page and regular page)
* CD slip (CD envelope)
* ID card (employee card)

And what ever else you want to throw in.
Updates

Guys,

Something I missed from the brief.   The predominat color should be RED.

Also, have fun and play with the exclamation mark (!) of the logo. 

Hi guys, more comments:

Remember that Zelvo is a "creativity" agency, not in the advertising side but on the promotional side, and that should reflect on the stationary.

 I want a bold design.  Bold and yet crisp.

 

Guys, i just uploaded the Logo in AI format.

I Also uploaded the actual Zelvo Bis Card, wich I like.  So I will like to see some designs with that bis card approach.

Guys, I am so sorry, but I notice in your last post that I upladed a wrong design ("13154_promotions_group_zelvo_brief225630.ai").  The problem was that I asked the designer the file in AI format and he send me thw wrong file, and since I dont have Illustrator I could not verify it.

The differences are minor, I just already ask him the correct one (similar to the EPS file).

Sorry                                   

Just post the correct AI file : "Zelvo Logo.ai"

Reason: I'm expecting more designs to choose from and also I wont be available tomorrow to decide.

Reason: Sorry guys, but we are not there yet!

Target Market(s)

Marketing directors, Marketing Managers

Industry/Entity Type

Legal

Requirements
Must have
• Must work with the logo attached.
The predominat color should be RED.
Play and have fun with the exclamation mark (!).
Should not have
• * No old fonts

Should not be:
* boring
* Informal
* rigid

```html
<!DOCTYPE html>
<html lang="en">
<head>
<meta charset="utf-8">
<title>Zelvo Promotions Group – Presentation Folder</title>
<link rel="stylesheet" href="https://fonts.googleapis.com/css2?family=Cinzel:wght@400;600&family=Roboto:wght@400;900&display=swap">
<style>
  :root {
    --stage: #000000;
    --stage-glow: #2a2a2a;
    --cover: #0b0b0b;
    --cover-edge: #1c1c1c;
    --brand-red: #d42b2b;
    --brand-red-dark: #a81c1c;
    --paper: #ffffff;
    --paper-shade: #e9e6e0;
    --ink-light: #ffffff;
    --ink-soft: #f3d6d6;
  }
  * { box-sizing: border-box; margin: 0; padding: 0; }
  html, body {
    width: 1200px; height: 559px; overflow: hidden;
    background: radial-gradient(ellipse 60% 70% at 22% 20%, var(--stage-glow), var(--stage) 70%);
    font-family: "Roboto", Arial, sans-serif;
  }
  .canvas { position: relative; width: 1200px; height: 559px; }

  /* Closed folder – front cover */
  .folder-cover {
    position: absolute; left: 55px; top: 45px; width: 440px; height: 470px;
    background: linear-gradient(160deg, var(--cover-edge), var(--cover) 45%);
  }
  .cover-accent {
    position: absolute; left: 300px; top: 110px; width: 110px; height: 110px;
    border-radius: 50%; background: var(--brand-red);
  }
  .cover-tagline {
    position: absolute; left: 250px; top: 306px;
    font-family: "Cinzel", Georgia, serif; font-size: 13px; color: var(--ink-light);
    letter-spacing: 0.5px; white-space: nowrap;
  }
  .cover-band {
    position: absolute; left: 0; top: 330px; width: 100%; height: 62px;
    background: linear-gradient(180deg, var(--brand-red), var(--brand-red-dark));
    display: flex; align-items: center; padding: 0 14px;
  }
  .band-brand { display: flex; flex-direction: column; width: 90px; }
  .brand-name {
    font-weight: 900; font-size: 20px; color: var(--ink-light); line-height: 1;
    text-transform: lowercase;
  }
  .brand-sub { font-size: 6px; letter-spacing: 1.5px; color: var(--ink-light); text-transform: uppercase; margin-top: 3px; }
  .band-copy {
    border-left: 1px solid rgba(255,255,255,0.6); padding-left: 8px;
    width: 150px; display: flex; flex-direction: column; gap: 6px;
  }
  .band-copy p { font-size: 5.5px; line-height: 1.35; color: var(--ink-soft); }
  .band-brand--large { margin-left: auto; width: auto; align-items: flex-start; margin-right: 30px; }
  .band-brand--large .brand-name { font-size: 30px; }
  .band-brand--large .brand-sub { font-size: 7px; }

  /* Open folder – inside spread */
  .folder-inside { position: absolute; left: 622px; top: 80px; width: 552px; height: 420px; }
</style>
</head>
<body>
<main class="canvas">

  <section class="folder-cover" aria-label="Folder front cover">
    <div class="cover-accent"></div>
    <p class="cover-tagline">Your Tagline Goes Here</p>
    <div class="cover-band">
      <div class="band-brand">
        <span class="brand-name">zelvo</span>
        <span class="brand-sub">Promotions Group</span>
      </div>
      <div class="band-copy">
        <p>We plan and run promotional activity that puts brands in the hands of real shoppers, on the street and in store.</p>
        <p>Sampling, events, retail displays and field teams, built fast and delivered with care across every market.</p>
      </div>
      <div class="band-brand band-brand--large">
        <span class="brand-name">zelvo</span>
        <span class="brand-sub">Promotions Group</span>
      </div>
    </div>
  </section>

  <svg class="folder-inside" viewBox="0 0 552 420" aria-label="Folder inside spread with pockets">
    <defs>
      <linearGradient id="leftPanel" x1="0" x2="1">
        <stop offset="0" stop-color="var(--paper)"/>
        <stop offset="0.8" stop-color="var(--paper)"/>
        <stop offset="1" stop-color="var(--paper-shade)"/>
      </linearGradient>
      <linearGradient id="rightPanel" x1="0" x2="1">
        <stop offset="0" stop-color="var(--paper-shade)"/>
        <stop offset="0.2" stop-color="var(--paper)"/>
      </linearGradient>
    </defs>
    <rect class="panel-left" x="0" y="0" width="276" height="420" fill="url(#leftPanel)"/>
    <rect class="panel-right" x="276" y="0" width="276" height="420" fill="url(#rightPanel)"/>
    <path class="pocket-left" d="M0 290 H240 L272 420 H0 Z" fill="var(--cover)"/>
    <path class="pocket-right" d="M312 290 H552 V420 H280 Z" fill="var(--cover)"/>
  </svg>

</main>
</body>
</html>
```